Psychotherapy, Life Coaching, Writer, Motivational Speaker

I am a psychotherapist, life coach, writer and speaker on health and wellness issues. I am a humanist - who believes that we are born to self-actualize - but life - changes that course. That we develop armor and coping mechanisms that divert our growth. I help people examine their road blocks to happiness. My business is unique in that I do concierge therapy. I work intensively - with multi-day sessions, I work internationally through tele-therapy - and traditionally - in an office space. My work is tailored to your needs.

Target Market(s)

Broad

Industry/Entity Type

Health

Contact Information for Business Card

Listen And Grow
Sam Perriton
248 East 39th Street
New York, NY 10027
(305) 555-0173

Requirements
Must have
• Clean lines... not too busy...
• FB page listing: Listen And Grow
• my Web page: www.listenandgrow-example.com
Nice to have
• I would love to be able to list the services: Psychotherapist, Life Coach, Motivational Speaker and Writer - but also don't want a crazy crowded card. Feel free to use the back for description.
Should not have
• Stay away from corny imagery - lotus flowers, zen, lily pond, clouds.

```html
<!DOCTYPE html>
<html lang="en">
<head>
<meta charset="utf-8">
<title>Listen And Grow – Business Card</title>
<link href="https://fonts.googleapis.com/css2?family=Lato:wght@400;700;900&display=swap" rel="stylesheet">
<style>
  :root {
    --backdrop: #e8e8e9;
    --card: #ffffff;
    --brand-blue: #4673ad;
    --blue-light: #6390c6;
    --blue-deep: #3c68a6;
    --brand-green: #58a443;
    --name-green: #8fe06f;
    --ink: #1c1c1c;
    --crescent: #0d0d0d;
    --band-text: #e6eef8;
  }
  * { margin: 0; padding: 0; box-sizing: border-box; }
  html, body { width: 1200px; height: 720px; overflow: hidden; }
  body {
    background: var(--backdrop);
    font-family: "Lato", Arial, sans-serif;
    color: var(--ink);
    position: relative;
  }
  .card {
    position: absolute;
    top: 241px;
    width: 419px;
    height: 239px;
    background: var(--card);
    border-radius: 14px;
    overflow: hidden;
  }
  .card--front { left: 148px; }
  .card--back { left: 633px; }

  .front-art { position: absolute; inset: 0; z-index: 0; }

  .brand-title {
    position: absolute;
    z-index: 1;
    left: 13px;
    top: 37px;
    font-size: 20px;
    font-weight: 700;
    color: var(--brand-blue);
    white-space: nowrap;
  }
  .contact-list {
    position: absolute;
    z-index: 1;
    left: 10px;
    top: 87px;
    list-style: none;
    font-size: 12.5px;
    line-height: 16px;
    white-space: nowrap;
  }
  .contact-list li { display: flex; align-items: center; gap: 4px; }
  .contact-icon { width: 10px; height: 10px; flex: none; }
  .contact-square { width: 9px; height: 9px; background: var(--brand-green); border-radius: 2px; flex: none; margin: 0 1px 0 0; }

  .address {
    position: absolute;
    z-index: 1;
    left: 12px;
    top: 181px;
    font-size: 12px;
    line-height: 15px;
    font-style: normal;
    white-space: nowrap;
  }

  .practitioner {
    position: absolute;
    z-index: 1;
    right: 12px;
    top: 107px;
    text-align: right;
    color: #ffffff;
    font-size: 13.5px;
    line-height: 17px;
    white-space: nowrap;
  }
  .practitioner-name {
    color: var(--name-green);
    font-weight: 900;
    font-size: 14.5px;
    text-shadow: 0 1px 2px rgba(20, 40, 80, 0.55);
  }

  .back-title {
    position: absolute;
    left: 0; right: 0;
    top: 56px;
    text-align: center;
    font-size: 20px;
    font-weight: 700;
    color: var(--brand-green);
  }
  .appointment-line {
    position: absolute;
    left: 0; right: 0;
    top: 132px;
    text-align: center;
    font-size: 14px;
    white-space: nowrap;
  }
  .services-band {
    position: absolute;
    left: 0; right: 0; bottom: 0;
    height: 34px;
    background: linear-gradient(90deg, var(--blue-deep), var(--blue-light) 50%, var(--blue-deep));
    color: var(--band-text);
    font-size: 13.5px;
    text-align: center;
    line-height: 34px;
  }
</style>
</head>
<body>

  <section class="card card--front">
    <svg class="front-art" width="419" height="239" viewBox="0 0 419 239" aria-hidden="true">
      <defs>
        <linearGradient id="blueSweep" x1="0" y1="0" x2="1" y2="1">
          <stop offset="0" stop-color="#4a77b2"/>
          <stop offset="1" stop-color="#6690c6"/>
        </linearGradient>
      </defs>
      <path d="M252 0 L284 0 C238 42 220 130 238 210 C216 140 222 52 252 0 Z" fill="var(--crescent)"/>
      <path d="M284 0 H419 V239 H254 C222 170 226 60 284 0 Z" fill="url(#blueSweep)"/>
    </svg>

    <h1 class="brand-title">Listen And Grow</h1>

    <ul class="contact-list">
      <li>
        <svg class="contact-icon" viewBox="0 0 12 12"><path d="M3 1 L5 3.5 L4 4.8 C4.8 6.4 5.8 7.4 7.2 8 L8.5 7 L11 9 L9.8 11 C5 10.6 1.4 7 1 2.2 Z" fill="var(--brand-green)"/></svg>
        (305) 555-0173
      </li>
      <li>
        <svg class="contact-icon" viewBox="0 0 12 12"><rect x="0.5" y="2" width="11" height="8" rx="1" fill="var(--brand-green)"/><path d="M1 2.5 L6 6.5 L11 2.5" stroke="#fff" stroke-width="1" fill="none"/></svg>
        sperriton.care@example.com
      </li>
      <li>
        <svg class="contact-icon" viewBox="0 0 12 12"><circle cx="6" cy="6" r="5.5" fill="var(--brand-green)"/><path d="M0.5 6 H11.5 M6 0.5 C3 3 3 9 6 11.5 M6 0.5 C9 3 9 9 6 11.5" stroke="#fff" stroke-width="0.8" fill="none"/></svg>
        www.listenandgrow-example.com
      </li>
      <li>
        <span class="contact-square"></span>
        Listen And Grow
      </li>
    </ul>

    <address class="address">
      248 East 39th Street<br>
      Suite #2B New York, NY 10027
    </address>

    <div class="practitioner">
      <span class="practitioner-name">Sam Perriton,</span> LMHC, NCC<br>
      Psychotherapist.
    </div>
  </section>

  <section class="card card--back">
    <h2 class="back-title">Listen and Grow</h2>
    <p class="appointment-line">Your Next Appoinment is at...................... at.............. am/pm</p>
    <div class="services-band">Psychotherapy, Coaching, Wellness Media</div>
  </section>

</body>
</html>
```